Website for new child psychology practice

New clinical psychology practice in NSW Australia, specialising in work with children, adolescents and families. I would like to feature the colours in the logo, which was recently designed by pixelharbor designer Odette.
I am seeking a professional looking page, which is easy to navigate and is colourful and playful but not childish.
Target Market(s)
Parents and professionals
Industry/Entity Type
Health
Coding
Coded - Design and coding required
Number of Pages Required
1 page
Font styles to use
Serif
Requirements
Must have
- Pages for 'About us' 'Services' 'Fees and information' 'Contact us'
Should not have
- Childish stock photos

```html
<!DOCTYPE html>
<html lang="en">
<head>
<meta charset="utf-8">
<title>Dr Clara Benton – Clinical Psychologist</title>
<link href="https://fonts.googleapis.com/css2?family=Cinzel:wght@600;700&family=Lato:wght@400;700&display=swap" rel="stylesheet">
<style>
:root{
  --magenta:#93186f;
  --magenta-deep:#7a1460;
  --red:#d2373c;
  --ink:#1d1d1d;
  --muted:#6b6b6b;
  --line:#a3196f;
  --field:#ffffff;
  --page:#ffffff;
  --footer:#000000;
  --grad:linear-gradient(90deg,#d23940,#9a1a73);
}
*{margin:0;padding:0;box-sizing:border-box}
html,body{width:1200px;height:3707px;overflow:hidden}
body{position:relative;background:var(--page);font-family:'Lato',sans-serif;color:var(--ink)}
.abs{position:absolute}
.top-rule{left:0;top:0;width:1200px;height:4px;background:var(--magenta)}
.brand{display:flex;align-items:center;gap:10px;font-family:'Cinzel',serif;font-weight:600;color:var(--ink);white-space:nowrap}
.brand .dot{width:30px;height:30px;border-radius:50%;background:var(--magenta)}
.site-brand{left:112px;top:38px;font-size:29px}
.main-nav{right:111px;top:48px;display:flex;gap:33px;font-size:16.5px}
.main-nav a,.footer-nav a{color:var(--ink);text-decoration:none}
.hero{left:0;top:117px;width:1200px;height:623px;background:linear-gradient(110deg,#c9c3bb 0%,#dedad4 35%,#ecebe8 60%,#e4e2de 100%)}
.hero-title{right:112px;top:222px;text-align:right;font-family:'Cinzel',serif;font-weight:700;font-size:53px;line-height:74px;color:#111}
.hero-text{right:112px;top:462px;text-align:right;font-size:18px;line-height:37px;color:#333;width:480px}
.btn{display:inline-flex;align-items:center;justify-content:center;border-radius:22px;background:var(--grad);color:#fff;font-weight:700;text-decoration:none}
.hero-btn{left:933px;top:555px;width:154px;height:41px;font-size:17px}
.hero-wave{left:0;top:660px;width:1200px;height:82px}
.section-title{font-family:'Cinzel',serif;font-weight:700;font-size:46px;color:#111}
.rule{height:2px;width:58px;background:var(--line)}
.services-title{left:110px;top:898px}
.services-rule{left:110px;top:965px}
.services-intro{left:510px;top:857px;width:585px;font-size:16px;line-height:31px;color:#555}
.card{width:307px;height:367px;background:#fff;box-shadow:0 0 14px rgba(0,0,0,.07)}
.card-photo{width:269px;height:216px}
.card h3{position:absolute;left:19px;top:182px;font-size:17.5px;font-weight:400;color:#111}
.card p{position:absolute;left:19px;top:215px;width:270px;font-size:12.5px;line-height:23px;color:var(--muted)}
.card .btn{position:absolute;left:22px;bottom:-16px;width:108px;height:31px;font-size:13px}
.about{left:0;top:2101px;width:1200px;height:502px;background:var(--magenta)}
.about-photo{left:0;top:2101px;width:620px;height:502px;background:radial-gradient(ellipse at 45% 50%,#5c1049 0%,#7c1662 45%,#93186f 80%)}
.about-title{left:653px;top:2222px;color:#fff}
.about-rule{left:653px;top:2287px;background:#fff}
.about-text{left:653px;top:2318px;width:440px;font-size:14px;line-height:31px;color:#fff}
.btn-light{left:653px;top:2501px;width:128px;height:42px;border-radius:22px;background:#fff;color:var(--magenta);font-size:16px;display:flex;align-items:center;justify-content:center}
.contact-title{left:0;top:2750px;width:1200px;text-align:center}
.contact-rule-l{left:357px;top:2779px}
.contact-rule-r{left:786px;top:2779px}
.field{background:var(--field);box-shadow:0 0 14px rgba(0,0,0,.07);font-size:12.5px;color:#555;padding:22px 33px}
.submit{left:537px;top:3187px;width:128px;height:42px;font-size:16px}
.footer-wave{left:0;top:3320px;width:1200px;height:80px}
.footer{left:0;top:3395px;width:1200px;height:312px;background:var(--footer)}
.footer-brand{left:0;top:3450px;width:1200px;justify-content:center;color:#fff;font-size:36px}
.footer-brand .dot{width:38px;height:38px}
.footer-nav{left:0;top:3550px;width:1200px;display:flex;justify-content:center;gap:33px;font-size:16.5px}
.footer-nav a{color:#fff}
.socials{left:0;top:3599px;width:1200px;display:flex;justify-content:center;gap:5px}
.socials span{width:36px;height:36px;border-radius:50%;background:var(--magenta)}
.socials span:nth-child(2){background:var(--red)}
.copyright{left:0;top:3660px;width:1200px;text-align:center;font-size:12.5px;color:#fff}
</style>
</head>
<body>
<div class="abs top-rule"></div>

<header>
  <div class="abs brand site-brand"><span class="dot"></span>Dr Clara Benton</div>
  <nav class="abs main-nav">
    <a href="#">Home</a><a href="#">About us</a><a href="#">Services</a><a href="#">Fees And Information</a><a href="#">Contact Us</a>
  </nav>
</header>

<section>
  <div class="abs hero" role="img" aria-label="Psychologist seated in an armchair with a clipboard in a bright consulting room"></div>
  <h1 class="abs hero-title">Clinical<br>Psychologist In<br>NSW Australia</h1>
  <p class="abs hero-text">Sed ut perspiciatis unde omnis iste natus error sit voluptatem accusantium doloremque laudantium, totam</p>
  <a class="abs btn hero-btn" href="#">Get Started</a>
  <svg class="abs hero-wave" viewBox="0 0 1200 82" preserveAspectRatio="none" aria-hidden="true">
    <defs><linearGradient id="hw" x1="0" x2="1"><stop offset="0" stop-color="#a01a73"/><stop offset=".5" stop-color="#c22a52"/><stop offset="1" stop-color="#d2373c"/></linearGradient></defs>
    <path d="M0,70 C120,30 260,20 400,50 C520,5 720,-5 900,28 C1020,45 1110,15 1200,0 L1200,82 L0,82Z" fill="url(#hw)"/>
    <path d="M0,82 L0,82 C140,60 280,55 420,78 C560,40 760,30 920,55 C1040,68 1130,45 1200,30 L1200,82Z" fill="#fff"/>
  </svg>
</section>

<section>
  <h2 class="abs section-title services-title">Our Services</h2>
  <div class="abs rule services-rule"></div>
  <p class="abs services-intro">Sed ut perspiciatis unde omnis iste natus error sit voluptatem accusantium doloremque laudantium, totam rem aperiam, eaque ipsa quae ab illo inventore veritatis et quasi architecto beatae vitae dicta sunt expl</p>

  <div class="abs card" style="left:110px;top:1086px"><h3>Dolorem ipsum quia dolor</h3><p>Occasionally circumstances occur in which toil and pain can procure him some great pleasure. To take a trivial example, which of us ever undertakes laborious physical exercise, except to obtain some advantage</p><a class="btn" href="#">Read More</a></div>
  <div class="abs card" style="left:452px;top:1086px"><h3>Dolorem ipsum quia dolor</h3><p>Occasionally circumstances occur in which toil and pain can procure him some great pleasure. To take a trivial example, which of us ever undertakes laborious physical exercise, except to obtain some advantage</p><a class="btn" href="#">Read More</a></div>
  <div class="abs card" style="left:794px;top:1086px"><h3>Dolorem ipsum quia dolor</h3><p>Occasionally circumstances occur in which toil and pain can procure him some great pleasure. To take a trivial example, which of us ever undertakes laborious physical exercise, except to obtain some advantage</p><a class="btn" href="#">Read More</a></div>
  <div class="abs card" style="left:110px;top:1588px"><h3>Dolorem ipsum quia dolor</h3><p>Occasionally circumstances occur in which toil and pain can procure him some great pleasure. To take a trivial example, which of us ever undertakes laborious physical exercise, except to obtain some advantage</p><a class="btn" href="#">Read More</a></div>
  <div class="abs card" style="left:452px;top:1588px"><h3>Dolorem ipsum quia dolor</h3><p>Occasionally circumstances occur in which toil and pain can procure him some great pleasure. To take a trivial example, which of us ever undertakes laborious physical exercise, except to obtain some advantage</p><a class="btn" href="#">Read More</a></div>
  <div class="abs card" style="left:794px;top:1588px"><h3>Dolorem ipsum quia dolor</h3><p>Occasionally circumstances occur in which toil and pain can procure him some great pleasure. To take a trivial example, which of us ever undertakes laborious physical exercise, except to obtain some advantage</p><a class="btn" href="#">Read More</a></div>

  <div class="abs card-photo" style="left:130px;top:1027px;background:linear-gradient(135deg,#cfc9c0,#8d8781)" role="img" aria-label="Two adults talking in armchairs during a session"></div>
  <div class="abs card-photo" style="left:472px;top:1027px;background:linear-gradient(135deg,#d9d3c9,#7f8e9a)" role="img" aria-label="Therapist taking notes while a child plays on the floor"></div>
  <div class="abs card-photo" style="left:814px;top:1027px;background:linear-gradient(135deg,#e9e6e3,#7a5c4c)" role="img" aria-label="Psychologist in a white coat listening at a desk"></div>
  <div class="abs card-photo" style="left:130px;top:1530px;background:linear-gradient(135deg,#d7c7b3,#6b5040)" role="img" aria-label="Family session with a young child on a sofa"></div>
  <div class="abs card-photo" style="left:472px;top:1530px;background:linear-gradient(135deg,#e6e3df,#9c9894)" role="img" aria-label="Counsellor and girl talking at a round table"></div>
  <div class="abs card-photo" style="left:814px;top:1530px;background:linear-gradient(135deg,#6d4b35,#3a2c24)" role="img" aria-label="Close view of hands clasped in support"></div>
</section>

<section>
  <div class="abs about"></div>
  <div class="abs about-photo" role="img" aria-label="Hands joined together in a circle, tinted magenta"></div>
  <h2 class="abs section-title about-title">About Us</h2>
  <div class="abs rule about-rule"></div>
  <p class="abs about-text">Sed ut perspiciatis unde omnis iste natus error sit voluptatem accusantium doloremque laudantium, totam rem aperiam, eaque ipsa quae ab illo inventore veritatis et quasi architecto beatae vitae dicta sunt exploed ut perspiciatis unde omnis iste natus error sit voluptatem accusantium doloremque laudantium, totam rem</p>
  <a class="abs btn-light" href="#" style="text-decoration:none">Read More</a>
</section>

<section>
  <h2 class="abs section-title contact-title">Contact Us</h2>
  <div class="abs rule contact-rule-l"></div>
  <div class="abs rule contact-rule-r"></div>
  <div class="abs field" style="left:178px;top:2855px;width:399px;height:60px">First Name</div>
  <div class="abs field" style="left:623px;top:2855px;width:400px;height:60px">Last Name</div>
  <div class="abs field" style="left:178px;top:2935px;width:399px;height:60px">Contact Number</div>
  <div class="abs field" style="left:623px;top:2935px;width:400px;height:60px">Email Address</div>
  <div class="abs field" style="left:178px;top:3016px;width:845px;height:194px;padding-top:20px">Comments....</div>
  <a class="abs btn submit" href="#">Submit Now</a>
</section>

<footer>
  <svg class="abs footer-wave" viewBox="0 0 1200 80" preserveAspectRatio="none" aria-hidden="true">
    <defs><linearGradient id="fw" x1="0" x2="1"><stop offset="0" stop-color="#9a1a73"/><stop offset=".6" stop-color="#b8245c"/><stop offset="1" stop-color="#c92d4a"/></linearGradient></defs>
    <path d="M0,38 C120,5 260,10 360,35 C520,0 760,-5 900,25 C1020,50 1120,20 1200,5 L1200,80 L0,80Z" fill="url(#fw)"/>
    <path d="M0,80 L0,70 C150,40 330,50 500,45 C640,10 780,10 900,40 C1020,65 1120,40 1200,25 L1200,80Z" fill="#000"/>
  </svg>
  <div class="abs footer"></div>
  <div class="abs brand footer-brand"><span class="dot"></span>Dr Clara Benton</div>
  <nav class="abs footer-nav">
    <a href="#">Home</a><a href="#">About us</a><a href="#">Services</a><a href="#">Fees And Information</a><a href="#">Contact Us</a>
  </nav>
  <div class="abs socials"><span></span><span></span><span></span></div>
  <p class="abs copyright">(C) Copyright 2024 | All Rights Reserved</p>
</footer>
</body>
</html>
```